Option Sheet

We need a one page option sheet with a left to right reading of the five options. It should be a one sheet, multiple colors and definitive separations between options This is used in a sales consultation. Backround or colors not in option need to have the follow RGB value (5 red, 20 green, 63 blue)

We added a smaller text file, please change that point

Target Market(s)

Divorce

Industry/Entity Type

Legal

Requirements
Must have
• 1) All five options left to right
• 2)language included in sheet

```html
<!DOCTYPE html>
<html lang="en">
<head>
<meta charset="UTF-8">
<title>Five Options – Divorce</title>
<link href="https://fonts.googleapis.com/css2?family=Montserrat:ital,wght@0,500;0,600;0,700;1,500&family=Source+Sans+3:wght@400&display=swap" rel="stylesheet">
<style>
  :root {
    --navy: rgb(5, 20, 63);
    --white: #ffffff;
    --text: #5a5a5f;
    --muted: #6f7080;
    --rule: #ececef;
    --divider: #e4e4e8;
    --orange: #f4502a;
    --pink: #d6489e;
    --indigo: #4b3b96;
    --lime: #7dc242;
    --green: #0f9146;
  }
  * { margin: 0; padding: 0; box-sizing: border-box; }
  html, body { width: 1200px; height: 671px; overflow: hidden; background: var(--white); }
  .sheet { position: relative; width: 1200px; height: 671px; background: var(--white); }
  .hero {
    position: absolute; left: 0; top: 0; width: 1200px; height: 384px;
    background: var(--navy); text-align: center; color: var(--white);
    font-family: "Montserrat", sans-serif;
  }
  .hero__kicker { position: absolute; top: 80px; width: 100%; font-size: 26px; font-weight: 500; line-height: 30px; }
  .hero__title { position: absolute; top: 117px; width: 100%; font-size: 52px; font-weight: 700; line-height: 60px; letter-spacing: 0.5px; }
  .card {
    position: absolute; left: 32px; top: 226px; width: 1136px; height: 445px;
    background: var(--white); border-radius: 6px 6px 0 0;
  }
  .options { position: absolute; left: 34px; top: 30px; display: flex; }
  .option { position: relative; width: 219.3px; }
  .option + .option::before {
    content: ""; position: absolute; left: 0; top: 13px; width: 1px; height: 290px; background: var(--divider);
  }
  .option__inner { width: 191px; }
  .option + .option .option__inner { margin-left: 14px; }
  .option__head { height: 51px; text-align: center; border-bottom: 1px solid var(--rule); font-family: "Montserrat", sans-serif; }
  .option__num { display: block; margin-top: 1px; font-size: 10.5px; font-style: italic; font-weight: 500; color: var(--muted); line-height: 12px; }
  .option__name { display: block; margin-top: 4px; font-size: 17px; font-weight: 600; line-height: 20px; white-space: nowrap; letter-spacing: -0.1px; }
  .option--limited .option__name { font-size: 16px; letter-spacing: -0.35px; }
  .section { padding-top: 19.5px; border-bottom: 1px solid var(--rule); }
  .section:last-child { border-bottom: 0; }
  .section__label { font-family: "Montserrat", sans-serif; font-size: 10.5px; font-weight: 600; line-height: 13px; letter-spacing: 0.3px; margin-bottom: 11px; }
  .points { list-style: none; padding-left: 6px; }
  .points li {
    position: relative; padding-left: 11px; margin-bottom: 8.3px; white-space: nowrap;
    font-family: "Source Sans 3", sans-serif; font-size: 10px; line-height: 12.3px; color: var(--text);
  }
  .points li::before {
    content: ""; position: absolute; left: 0; top: 3.2px; width: 6px; height: 6px; border-radius: 50%; background: var(--accent);
  }
  .points li.plain::before { display: none; }
  .adv { height: 97px; }
  .option--limited .adv { height: 93px; }
  .option--hire .adv { height: 156px; }
  .option--hire .disadv { padding-top: 22.5px; }
  .option--nothing { --accent: var(--orange); }
  .option--counsel { --accent: var(--pink); }
  .option--diy { --accent: var(--indigo); }
  .option--limited { --accent: var(--lime); }
  .option--hire { --accent: var(--green); }
  .option__name, .section__label { color: var(--accent); }
</style>
</head>
<body>
<div class="sheet">
  <header class="hero">
    <p class="hero__kicker">Five Options</p>
    <h1 class="hero__title">DIVORCE</h1>
  </header>
  <main class="card">
    <div class="options">
      <section class="option option--nothing"><div class="option__inner">
        <div class="option__head"><span class="option__num">Option #1</span><span class="option__name">Do Nothing</span></div>
        <div class="section adv"><h3 class="section__label">Advantages:</h3>
          <ul class="points"><li>Stay married</li><li>No life Changes</li></ul></div>
        <div class="section disadv"><h3 class="section__label">Disadvantages:</h3>
          <ul class="points"><li>Remain unhappy, depressed, anxious</li><li>Money and assets may disappear</li><li>What is going to change?</li></ul></div>
      </div></section>
      <section class="option option--counsel"><div class="option__inner">
        <div class="option__head"><span class="option__num">Option #2</span><span class="option__name">Go to Counseling</span></div>
        <div class="section adv"><h3 class="section__label">Advantages:</h3>
          <ul class="points"><li>Reconcile marriage</li><li>Help make a better life</li></ul></div>
        <div class="section disadv"><h3 class="section__label">Disadvantages:</h3>
          <ul class="points"><li>Past issues are highlighted and may<br>drudge up old wounds</li><li>It may just clarify the reasons you need to<br>separate and/or divorce</li><li>Both parties must be invested and<br>willing to participate</li></ul></div>
      </div></section>
      <section class="option option--diy"><div class="option__inner">
        <div class="option__head"><span class="option__num">Option #3</span><span class="option__name">Do it Yourself</span></div>
        <div class="section adv"><h3 class="section__label">Advantages:</h3>
          <ul class="points"><li>No attorney fees</li><li>You are your on attorney</li></ul></div>
        <div class="section disadv"><h3 class="section__label">Disadvantages:</h3>
          <ul class="points"><li>People often find that what is “fair,”<br>may in fact, not be truly fair</li><li>Often times, people do not know the risks</li><li>Complicated legal system within intrigue<br>rules</li><li class="plain">Unsure how to complete the necessary<br>paperwork and meet the deadlines</li></ul></div>
      </div></section>
      <section class="option option--limited"><div class="option__inner">
        <div class="option__head"><span class="option__num">Option #4</span><span class="option__name">Limited Representation</span></div>
        <div class="section adv"><h3 class="section__label">Advantages:</h3>
          <ul class="points"><li>Balance between going alone and our<br>limited involvement in the case</li></ul></div>
        <div class="section disadv"><h3 class="section__label">Disadvantages:</h3>
          <ul class="points"><li>Our terms may not benefit from our<br>legal knowledge</li><li>The legal consequences of yourlegal<br>documents will not be explained to you<br>so that you can formulate a plan for<br>handling the rest of your case.</li><li>Your spouse or other parties may cause<br>your legal fees to increase significantly<br>without action on your part</li></ul></div>
      </div></section>
      <section class="option option--hire"><div class="option__inner">
        <div class="option__head"><span class="option__num">Option #5</span><span class="option__name">Hire Us</span></div>
        <div class="section adv"><h3 class="section__label">Advantages:</h3>
          <ul class="points"><li>Gain the full benefits of our experience</li><li>Have a team of Family Law focus attorneys</li><li>Often saves you or makes you money<br>in the long run</li><li>Save you time, energy and stress</li></ul></div>
        <div class="section disadv"><h3 class="section__label">Disadvantages:</h3>
          <ul class="points"><li>Initial cost</li></ul></div>
      </div></section>
    </div>
  </main>
</div>
</body>
</html>
```